Real estate broker business card

Want a modern celan but effective business card for my residential and commercial real estate business. I want the back of the card to advertise my services and to capture business. I have attached the back of my current business card fore ideas
Updates

Logos, photo and text updates added! Added Saturday, September 3, 2016

Project Deadline Extended Reason: LOGOS, PHOTOS AND TEST JUST UPLOADED! I'M READY TO PICK A DESIGN! THANK YOU! Added Saturday, September 3, 2016

Target Market(s)

home buyers and seller. commercial buyers and sellers

Industry/Entity Type

Real Estate

Contact Information for Business Card

must have my contact information and my photo

Requirements
Must have
• Carla Ventrino
• Owner & Qualifying Broker
• Ventrino Real Estate Services
• 505.718.2094
• carla@ventrinohomes.example
• www.ventrinohomes.example
Nice to have
• metallic
• Business capture text: " Don't buy or lease property without someone looking out for your best interests. I will represent you on your home or investment purchase for FREE!"
• "Home owners, call today to receive a FREE market analysis for your homes value!

```html
<!DOCTYPE html>
<html lang="en">
<head>
<meta charset="utf-8">
<title>Ventrino Real Estate Services – Business Card</title>
<link rel="stylesheet" href="https://fonts.googleapis.com/css2?family=Cinzel:wght@600&family=Source+Sans+3:wght@400&display=swap">
<style>
  :root {
    --page-bg: #e9e6e4;
    --card-black: #060707;
    --teal: #1f8793;
    --teal-bright: #2aa0ad;
    --text-light: #c9cdcf;
    --text-dark: #1b1b1b;
    --band-grey: #e3e3e5;
    --white: #ffffff;
  }
  * { box-sizing: border-box; margin: 0; padding: 0; }
  html, body { width: 1200px; height: 1200px; overflow: hidden; }
  body {
    background: var(--page-bg);
    font-family: "Source Sans 3", "Myriad Pro", sans-serif;
    position: relative;
  }
  .card {
    position: absolute;
    left: 259px;
    width: 682px;
    height: 386px;
    border-radius: 20px;
    overflow: hidden;
    box-shadow: 0 4px 12px rgba(0,0,0,0.25);
  }

  /* Company name block */
  .company-mark {
    position: absolute;
    display: flex;
    align-items: center;
    gap: 12px;
  }
  .company-mark__dot {
    flex: none;
    border-radius: 50%;
    background: var(--teal);
  }
  .company-mark__name {
    font-family: "Source Sans 3", sans-serif;
    font-weight: 400;
    color: var(--teal-bright);
    white-space: nowrap;
    line-height: 1;
  }

  /* Front */
  .card--front { top: 210px; background: var(--card-black); }
  .card--front .company-mark { left: 30px; top: 62px; }
  .card--front .company-mark__dot { width: 44px; height: 44px; }
  .card--front .company-mark__name { font-size: 25px; }

  .portrait {
    position: absolute;
    left: 357px; top: 0; width: 325px; height: 386px;
    background: linear-gradient(165deg, #243324 0%, #2f3d2b 45%, #3a322c 75%, #8d8783 100%);
  }
  .portrait::before {
    content: ""; position: absolute; inset: 0;
    background: linear-gradient(90deg, var(--card-black) 0%, rgba(6,7,7,0) 22%);
  }
  .name-band {
    position: absolute;
    left: 0; top: 159px; width: 500px; height: 78px;
    background: linear-gradient(90deg, var(--teal) 0%, #207a85 45%, rgba(31,135,147,0) 100%);
  }
  .agent-name {
    position: absolute; left: 32px; top: 172px;
    font-family: "Cinzel", serif; font-weight: 600;
    font-size: 26px; line-height: 30px; color: #0b0d0e; letter-spacing: 0.5px;
  }
  .agent-title {
    position: absolute; left: 32px; top: 204px;
    font-size: 17.5px; line-height: 22px; color: #0b0d0e;
  }
  .company-line {
    position: absolute; left: 30px; top: 249px;
    font-size: 17.5px; line-height: 22px; color: var(--text-light);
  }
  .contact-list { position: absolute; left: 30px; top: 285px; list-style: none; }
  .contact-list li {
    display: flex; align-items: center; gap: 8px;
    height: 23px; font-size: 17.5px; color: var(--text-light);
  }
  .contact-list svg { width: 18px; height: 18px; flex: none; }

  /* Back */
  .card--back { top: 663px; background: var(--white); }
  .card--back .company-mark {
    left: 0; right: 0; top: 36px;
    flex-direction: column; gap: 22px;
  }
  .card--back .company-mark__dot { width: 84px; height: 84px; }
  .card--back .company-mark__name { font-size: 32px; color: var(--teal); }

  .pitch-band {
    position: absolute; left: 0; top: 220px; width: 100%; height: 75px;
    background: var(--band-grey);
  }
  .pitch, .offer {
    position: absolute; left: 0; right: 0; text-align: center;
    font-size: 17.6px; line-height: 23px; color: var(--text-dark);
  }
  .pitch { top: 223px; }
  .offer { top: 307px; }
</style>
</head>
<body>
  <section class="card card--front">
    <div class="portrait" role="img" aria-label="Portrait photograph of the broker"></div>
    <div class="company-mark">
      <span class="company-mark__dot"></span>
      <span class="company-mark__name">Ventrino Real Estate Services</span>
    </div>
    <div class="name-band"></div>
    <h1 class="agent-name">Carla Ventrino</h1>
    <p class="agent-title">Owner &amp; Qualifying Broker</p>
    <p class="company-line">Ventrino Real Estate Services</p>
    <ul class="contact-list">
      <li>
        <svg viewBox="0 0 20 20" aria-hidden="true"><path fill="var(--teal-bright)" d="M2 7c0-3 16-3 16 0v2h-4V7.5c-2-1-6-1-8 0V9H2zM5 10h10l2 7H3z"/><circle cx="10" cy="13.5" r="2" fill="var(--card-black)"/></svg>
        505.718.2094
      </li>
      <li>
        <svg viewBox="0 0 20 20" aria-hidden="true"><rect x="1.5" y="4" width="17" height="12" fill="var(--teal-bright)"/><path d="M1.5 4l8.5 7 8.5-7M1.5 16l6-5.5M18.5 16l-6-5.5" stroke="var(--card-black)" stroke-width="1.3" fill="none"/></svg>
        carla@ventrinohomes.example
      </li>
      <li>
        <svg viewBox="0 0 20 20" aria-hidden="true" fill="none" stroke="var(--teal-bright)" stroke-width="1.4"><circle cx="10" cy="10" r="8"/><ellipse cx="10" cy="10" rx="3.5" ry="8"/><path d="M2 10h16M3.5 6h13M3.5 14h13"/></svg>
        www.ventrinohomes.example
      </li>
    </ul>
  </section>

  <section class="card card--back">
    <div class="company-mark">
      <span class="company-mark__dot"></span>
      <span class="company-mark__name">Ventrino Real Estate Services</span>
    </div>
    <div class="pitch-band"></div>
    <p class="pitch">Don't buy or lease property without someone looking out<br>for your best interests. I will represent you on your home<br>or investment purchase for FREE!</p>
    <p class="offer">Home owners, call today to receive a FREE market analysis<br>for your homes value!</p>
  </section>
</body>
</html>
```